RW Holloway LLC Business Card - Civil Engineering & Consulting Firm

We need a Business Card that is elegant, and masculine.  It is our Professional Civil Engineering & Consulting Company located in San Antonio TX (Not s construction or builder firm- no gears & no tool images please). We provide civil engineering services including  commercial site plans, grading and drainage plans, utility plans, hydraulics and hydrology, land planning, utility coordination, and other general civil engineering services related to commercial and residential development.
We have 2 existing Logos. We would like to convey reliability, strength, trustworthiness and attention to detail.  Blues and orange tones as per logo We are OK with the use of a darker blue in the mix.  We have 2 logo versions - Full Company Name Logo to go on the back of card, & Small Icon Logo for the front w/ personal Info.

Target Market(s)
Architects, Real Estate Developers, Other Strctural Engineers, Surveyers, General Contractors
Industry/Entity Type
Professional Civil Engineering
Contact Information for Business Card
Name, Position, Address, Cell & Office #, email, and company website
Font styles to use
Other font styles liked:
- Avian
Requirements
Should not have
- No Tools, No Gears, no Cranes, or Construction Equipment.

```html
<!DOCTYPE html>
<html lang="en">
<head>
<meta charset="utf-8">
<title>RW Holloway LLC – Business Card</title>
<link href="https://fonts.googleapis.com/css2?family=Montserrat:wght@400;500;700&display=swap" rel="stylesheet">
<style>
  :root {
    --bg: #d4d4d4;
    --white: #ffffff;
    --paper: #f4f3f2;
    --orange: #ee8f2c;
    --blue: #7aadd7;
    --ink: #1d1d1d;
    --back-top: #7f9fc0;
    --back-mid: #a89c93;
    --back-bottom: #e0964c;
  }
  * { box-sizing: border-box; margin: 0; padding: 0; }
  html, body { width: 1200px; height: 813px; overflow: hidden; }
  body {
    background: var(--bg);
    font-family: "Montserrat", sans-serif;
    position: relative;
  }
  .card {
    position: absolute;
    top: 246px;
    width: 560px;
    height: 320px;
    overflow: hidden;
    box-shadow: 0 10px 24px rgba(0,0,0,0.28);
  }
  .card--front { left: 25px; background: linear-gradient(120deg, var(--white) 45%, var(--paper)); }
  .card--back  { left: 615px; background: linear-gradient(170deg, var(--back-top) 0%, var(--back-mid) 45%, var(--back-bottom) 100%); }

  .front__decor {
    position: absolute; left: 0; top: 0;
    width: 300px; height: 128px;
    background: linear-gradient(20deg, var(--orange) 0%, #d9a06a 50%, var(--blue) 100%);
  }

  .holder { position: absolute; left: 30px; top: 34px; color: var(--white); }
  .holder__name { font-weight: 700; font-size: 19px; letter-spacing: 1px; text-transform: uppercase; }
  .holder__role { font-weight: 400; font-size: 15px; margin-top: 4px; }

  .contact { position: absolute; left: 36px; top: 160px; color: var(--ink); font-size: 14.5px; line-height: 20px; }
  .contact__address { margin-left: 30px; margin-bottom: 10px; }
  .contact__row { display: flex; align-items: center; gap: 10px; }
  .contact__icon { width: 20px; height: 19px; flex: none; }

  .front__mark {
    position: absolute; left: 330px; top: 70px;
    display: flex; align-items: center; gap: 10px;
    color: var(--orange); font-weight: 700; font-size: 19px; letter-spacing: 0.5px;
  }
  .front__mark-square { width: 14px; height: 14px; background: var(--blue); flex: none; }

  .back__name {
    position: absolute; inset: 0;
    display: flex; align-items: center; justify-content: center;
    color: var(--white); font-weight: 500; font-size: 36px; letter-spacing: 3px;
    text-transform: uppercase;
  }
</style>
</head>
<body>

<section class="card card--front" aria-label="Card front">
  <div class="front__decor" role="img" aria-label="Curved orange and blue swoosh decoration"></div>

  <div class="holder">
    <div class="holder__name">Dane Whitfield</div>
    <div class="holder__role">Co-Founder</div>
  </div>

  <div class="front__mark">
    <span class="front__mark-square"></span>
    <span>RW Holloway LLC</span>
  </div>

  <div class="contact">
    <p class="contact__address">4810 Ridgeline Drive<br>Suite 210 Alamo Heights</p>
    <p class="contact__row">
      <svg class="contact__icon" viewBox="0 0 20 20" aria-hidden="true"><path d="M5 2 L8 6 L6 8 C7 11 9 13 12 14 L14 12 L18 15 L16 18 C9 18 2 11 2 4 Z" fill="var(--orange)"/></svg>
      <span>210-555-0148</span>
    </p>
    <p class="contact__row">
      <svg class="contact__icon" viewBox="0 0 20 20" aria-hidden="true"><rect x="2" y="3" width="16" height="14" rx="2" fill="var(--orange)"/><rect x="5" y="6" width="10" height="4" fill="#fff"/><circle cx="10" cy="13" r="1.5" fill="#fff"/></svg>
      <span>210-555-0172</span>
    </p>
    <p class="contact__row">
      <svg class="contact__icon" viewBox="0 0 20 20" aria-hidden="true"><rect x="2" y="4" width="16" height="12" fill="var(--orange)"/><path d="M2 4 L10 11 L18 4" fill="none" stroke="#fff" stroke-width="1.5"/></svg>
      <span>info@rwhollowayllc.com</span>
    </p>
    <p class="contact__row">
      <svg class="contact__icon" viewBox="0 0 20 20" aria-hidden="true"><circle cx="10" cy="10" r="8" fill="var(--orange)"/><path d="M2 10 H18 M10 2 C6 6 6 14 10 18 M10 2 C14 6 14 14 10 18" fill="none" stroke="#fff" stroke-width="1.2"/></svg>
      <span>www.rwhollowayeng.com</span>
    </p>
  </div>
</section>

<section class="card card--back" aria-label="Card back">
  <div class="back__name">RW Holloway LLC</div>
</section>

</body>
</html>
```